Financial Coaching biz needs modern service presentation menu

We need a PowerPoint presentation document with a modern, easy-to-read layout to share with potential clients.

I have a website under development that can be used as a reference www.brightcoinharbor.com.

We'd like the doc to be simple to edit because services and verbiage will likely be modified periodically.

Two logo variations have been included.

Target Market(s)

Gen X, Gen Y, and Millienials

Industry/Entity Type

Financial Planning

Colors
85cae6
cadf82
ffffff
dddddd
cfcfcf
cee9f5

```html
<!DOCTYPE html>
<html lang="en">
<head>
<meta charset="utf-8">
<title>BrightCoin Harbor – Our Promise</title>
<link rel="stylesheet" href="https://fonts.googleapis.com/css2?family=PT+Sans:wght@700&display=swap">
<style>
  :root {
    --white: #ffffff;
    --band-grey: #d5d3d4;
    --panel-grey: #d3d1d2;
    --brand-green: #2bb673;
    --brand-blue: #23a7e0;
    --ink: #2b2b2b;
    --stamp: #3a3d40;
    --mascot-grey: #e4e4e4;
    --mascot-mint: #7fd1a8;
  }
  * { margin: 0; padding: 0; box-sizing: border-box; }
  html, body { width: 1200px; height: 848px; overflow: hidden; background: var(--white); }
  .slide { position: relative; width: 1200px; height: 848px; background: var(--white); overflow: hidden;
    font-family: "PT Sans", Arial, sans-serif; }

  .brand { position: absolute; left: 68px; top: 40px; display: flex; align-items: center; gap: 22px; }
  .brand-dot { width: 92px; height: 92px; border-radius: 50%; background: var(--mascot-grey); }
  .brand-name { font-weight: 700; font-size: 46px; line-height: 50px; color: var(--brand-green); letter-spacing: 1px; }

  .mascot-art { position: absolute; left: 766px; top: 0; width: 422px; height: 214px;
    border-radius: 0 0 40px 40px;
    background: linear-gradient(180deg, var(--mascot-grey) 0%, #dcdcdc 100%); }

  .band-top { position: absolute; left: 0; top: 214px; width: 100%; height: 18px; background: var(--band-grey); }
  .band-green { position: absolute; left: 0; top: 232px; width: 100%; height: 30px; background: var(--brand-green); }
  .panel { position: absolute; left: 0; top: 262px; width: 100%; height: 476px; background: var(--panel-grey); }
  .band-blue { position: absolute; left: 0; top: 738px; width: 100%; height: 32px; background: var(--brand-blue); }
  .band-bottom { position: absolute; left: 0; top: 770px; width: 100%; height: 14px; background: var(--band-grey); }

  .guarantee-seal { position: absolute; left: 80px; top: 328px; width: 316px; height: 316px; }

  .promise { position: absolute; left: 439px; top: 300px; width: 720px;
    font-weight: 700; font-size: 17.5px; line-height: 25.6px; color: var(--ink); letter-spacing: 0.9px; }
  .promise p + p { margin-top: 25.6px; }
</style>
</head>
<body>
<main class="slide">
  <header class="brand">
    <div class="brand-dot"></div>
    <div class="brand-name">BRIGHTCOIN<br>HARBOR</div>
  </header>

  <div class="mascot-art" role="img" aria-label="Large brand mascot decoration"></div>

  <div class="band-top"></div>
  <div class="band-green"></div>
  <section class="panel"></section>
  <div class="band-blue"></div>
  <div class="band-bottom"></div>

  <svg class="guarantee-seal" viewBox="0 0 316 316" role="img" aria-label="Satisfaction guarantee seal">
    <circle cx="158" cy="158" r="148" fill="none" stroke="var(--stamp)" stroke-width="14"/>
    <circle cx="158" cy="158" r="124" fill="none" stroke="var(--stamp)" stroke-width="4"/>
  </svg>

  <article class="promise">
    <p>We provide a FREE CONSULTATION and conduct a full assessment<br>before we take on any new client.&nbsp; Therefore, prospective clients<br>find out upfront if we can actually help them.</p>
    <p>We pride ourselves on being good corporate citizens as well.&nbsp; For<br>every new household we sign, we commit<br>to providing free service to household below the poverty line.</p>
    <p>Our promise is that we won't take on or charge a client a single cent<br>unless we are ABSOLUTELY SURE<br>we can add value.</p>
    <p>Our company is fundamentally built upon the service and the help<br>we provide.<br>So if we can't help you, we won't charge you.&nbsp; PERIOD.</p>
  </article>
</main>
</body>
</html>
```